Business card for law firm

Need business card for new law firm. Think confident, authoritative, conservative, but not stuffy or old-fashioned.

Contact Information for Business Card

Content for card - logo (uploaded), plus the following:

Paul Whitcombe (larger font)
Managing Partner (larger font, but not as large as name)
Level 9, 7 Ferris Lane
Sydney NSW 2000
Main Tel 02 9364 2710
Direct Tel 02 8472 3159
Email paul@qvlegal.com.au
www.qvlegal.com.au

Letterhead design should include logo plus:
Level 9, 7 Ferris Lane
Sydney NSW 2000
Tel 02 8472 3159
www.qvlegal.com.au

```html
<!DOCTYPE html>
<html lang="en">
<head>
<meta charset="utf-8">
<title>Quayview Legal – Business Card</title>
<link rel="stylesheet" href="https://fonts.googleapis.com/css2?family=Crimson+Pro:wght@400;500&family=Roboto:wght@400&display=swap">
<style>
  :root {
    --backdrop: #d1d2d4;
    --paper: #ffffff;
    --navy: #1e2250;
    --ink: #111111;
    --on-navy: #ffffff;
  }
  * { box-sizing: border-box; margin: 0; padding: 0; }
  html, body { width: 1200px; height: 1200px; overflow: hidden; }
  body { background: var(--backdrop); position: relative; font-family: "Roboto", Arial, sans-serif; }

  .card {
    position: absolute; left: 240px; top: 394px;
    width: 720px; height: 412px;
    display: flex;
  }
  .card__front { width: 360px; height: 100%; background: var(--paper); position: relative; }
  .card__contact { width: 360px; height: 100%; background: var(--navy); position: relative; color: var(--on-navy); }

  .person__name {
    position: absolute; left: 62px; top: 38px;
    font-family: "Crimson Pro", Georgia, serif; font-weight: 500;
    font-size: 41px; line-height: 1; color: var(--navy); white-space: nowrap;
  }
  .person__role {
    position: absolute; left: 62px; top: 80px;
    font-size: 27px; line-height: 1.1; color: var(--ink); white-space: nowrap;
  }

  .firm-mark {
    position: absolute; left: 0; right: 0; top: 198px;
    display: flex; flex-direction: column; align-items: center; gap: 22px;
  }
  .firm-mark__square { width: 58px; height: 58px; background: var(--navy); }
  .firm-mark__name {
    font-family: "Crimson Pro", Georgia, serif; font-weight: 400;
    font-size: 34px; letter-spacing: 2px; color: var(--ink); text-transform: uppercase; white-space: nowrap;
  }

  .contact-list { position: absolute; left: 56px; top: 110px; list-style: none; }
  .contact-item { position: absolute; left: 0; display: flex; align-items: flex-start; gap: 14px; font-size: 20px; line-height: 25px; white-space: nowrap; }
  .contact-item svg { flex: none; width: 28px; height: 28px; stroke: var(--on-navy); fill: none; stroke-width: 1.4; }
  .contact-item--phone { top: 0; }
  .contact-item--address { top: 66px; }
  .contact-item--email { top: 132px; }
  .contact-item--web { top: 180px; }
</style>
</head>
<body>
  <section class="card">
    <div class="card__front">
      <h1 class="person__name">Paul Whitcombe</h1>
      <p class="person__role">Managing Partner</p>
      <div class="firm-mark">
        <span class="firm-mark__square"></span>
        <span class="firm-mark__name">Quayview Legal</span>
      </div>
    </div>

    <div class="card__contact">
      <ul class="contact-list">
        <li class="contact-item contact-item--phone">
          <svg viewBox="0 0 28 28"><rect x="7" y="4" width="14" height="22" rx="4"/><rect x="10" y="8" width="8" height="6" rx="1"/><circle cx="14" cy="19.5" r="1.5"/><path d="M9 4V1"/></svg>
          <span>02 9364 2710<br>02 8472 3159</span>
        </li>
        <li class="contact-item contact-item--address">
          <svg viewBox="0 0 28 28"><path d="M14 27C8 19 5 15 5 10.5a9 9 0 0 1 18 0C23 15 20 19 14 27z"/><circle cx="14" cy="10.5" r="3.5"/></svg>
          <span>Level 9, 7 Ferris Lane<br>Sydney NSW 2000</span>
        </li>
        <li class="contact-item contact-item--email">
          <svg viewBox="0 0 28 28"><rect x="2" y="7" width="24" height="15"/><path d="M2 7l12 9 12-9"/></svg>
          <span>paul@qvlegal.com.au</span>
        </li>
        <li class="contact-item contact-item--web">
          <svg viewBox="0 0 28 28"><circle cx="14" cy="14" r="12"/><ellipse cx="14" cy="14" rx="5" ry="12"/><path d="M2 14h24M4 8h20M4 20h20"/></svg>
          <span>www.qvlegal.com.au</span>
        </li>
      </ul>
    </div>
  </section>
</body>
</html>
```